Foot doctor needs feet friendly business cards.

Business cards for Podiatrist. Needs to look professional and modern. Back side put an appointment card, and try to put a little basic street map somewhere on card along with all of our contact info below:

Marcus Dovan, DPM, Inc.
Diplomate, National Council of Lower Limb Medicine
Call: 1.877.Toes.482
1.555.283.9146
Fax: 1.555.671.3820
Email: info@DrDovanclinic.example
Web: www.DrDovanclinic.example
2847 W. Harbor Ln. Suite 204
Costa Mesa, CA 90000

```html
<!DOCTYPE html>
<html lang="en">
<head>
<meta charset="utf-8">
<title>Marcus Dovan, DPM – Business &amp; Appointment Card</title>
<link rel="stylesheet" href="https://fonts.googleapis.com/css2?family=Source+Sans+3:wght@400;600;700&display=swap">
<style>
  :root {
    --backdrop: #e9e7e4;
    --card-dark: #0f0f10;
    --card-light: #ffffff;
    --brand-blue: #2f5f93;
    --ink-light: #f2f2f2;
    --rule-dark: #3a3a3c;
    --rule-light: #6d86a8;
    --photo-top: #f7f4f1;
    --photo-mid: #e3bfa3;
    --photo-low: #c99878;
  }
  * { box-sizing: border-box; margin: 0; padding: 0; }
  html, body { width: 1200px; height: 900px; overflow: hidden; }
  body {
    background: var(--backdrop);
    font-family: "Source Sans 3", "Myriad Pro", sans-serif;
    position: relative;
  }
  .card {
    position: absolute;
    top: 296px;
    width: 540px;
    height: 309px;
    box-shadow: 0 6px 18px rgba(0,0,0,.18);
  }

  /* Front */
  .card--front { left: 40px; background: var(--card-dark); }
  .front__photo {
    position: absolute; left: 32px; top: 92px; width: 192px; height: 176px;
    background: linear-gradient(180deg, var(--photo-top) 0%, var(--photo-top) 25%, var(--photo-mid) 55%, var(--photo-low) 100%);
  }
  .front__divider {
    position: absolute; left: 244px; top: 22px; bottom: 22px; width: 1px;
    background: var(--rule-dark);
  }
  .front__details { position: absolute; left: 258px; top: 24px; right: 14px; color: var(--ink-light); }
  .front__name { color: var(--brand-blue); font-size: 20px; font-weight: 600; line-height: 1.1; }
  .front__title { font-size: 13.5px; line-height: 1.2; margin-top: 3px; }
  .front__address { font-size: 13.5px; line-height: 1.2; margin-top: 14px; }
  .contact { list-style: none; margin-top: 10px; font-size: 14.5px; }
  .contact li { display: flex; align-items: center; height: 21px; }
  .contact svg { width: 12px; height: 12px; margin-right: 10px; flex: none; }
  .contact .no-icon { padding-left: 22px; }

  /* Back */
  .card--back { left: 620px; background: var(--card-light); color: var(--brand-blue); }
  .back__heading {
    position: absolute; top: 32px; left: 0; right: 0; text-align: center;
    font-size: 15px; font-weight: 700; letter-spacing: .04em;
  }
  .field-rule { position: absolute; height: 1px; background: var(--rule-light); }
  .field-label { position: absolute; font-size: 14px; }
  .field-label--underlined { text-decoration: underline; }
  .back__note {
    position: absolute; top: 208px; left: 40px; right: 40px; text-align: center;
    font-size: 13.5px; line-height: 1.35;
  }
  .back__web { display: block; margin-top: 2px; }
</style>
</head>
<body>

<section class="card card--front" aria-label="Business card front">
  <div class="front__photo" role="img" aria-label="Photo of several bare feet resting together on white bedding"></div>
  <div class="front__divider"></div>
  <div class="front__details">
    <h1 class="front__name">Marcus Dovan, DPM, Inc.</h1>
    <p class="front__title">Diplomate, National Council<br>of Lower Limb Medicine</p>
    <p class="front__address">2847 W. Harbor Ln. Suite 204<br>Costa Mesa, CA 90000</p>
    <ul class="contact">
      <li class="no-icon">1.877.Toes.482</li>
      <li>
        <svg viewBox="0 0 12 12" aria-hidden="true"><path fill="#2f5f93" d="M1 4c0-2 2-3 5-3s5 1 5 3l-2 1-1-1.5H4L3 5zM3 6h6l1 5H2z"/></svg>
        1.555.283.9146
      </li>
      <li>
        <svg viewBox="0 0 12 12" aria-hidden="true"><path fill="#2f5f93" d="M3 1h5l1 1v3H3zM1 5h10v6H1zM3 7h2v1H3zm0 2h2v1H3zm4-2h2v3H7z"/></svg>
        1.555.671.3820
      </li>
      <li>
        <svg viewBox="0 0 12 12" aria-hidden="true"><rect x="1" y="2.5" width="10" height="7" fill="#2f5f93"/><path d="M1.5 3l4.5 3.5L10.5 3" fill="none" stroke="#0f0f10" stroke-width="1"/></svg>
        info@DrDovanclinic.example
      </li>
      <li>
        <svg viewBox="0 0 12 12" aria-hidden="true"><g fill="none" stroke="#2f5f93" stroke-width="1.6"><rect x="1" y="5.5" width="5" height="3" rx="1.5" transform="rotate(-45 3.5 7)"/><rect x="6" y="3.5" width="5" height="3" rx="1.5" transform="rotate(-45 8.5 5)"/></g></svg>
        www.DrDovanclinic.example
      </li>
    </ul>
  </div>
</section>

<section class="card card--back" aria-label="Appointment card">
  <h2 class="back__heading">APPOINTMENT</h2>
  <div class="field-rule" style="top:60px; left:150px; right:60px;"></div>
  <span class="field-label" style="top:70px; left:330px;">Time :</span>
  <div class="field-rule" style="top:90px; left:372px; right:40px;"></div>
  <span class="field-label field-label--underlined" style="top:108px; left:40px;">For :</span>
  <div class="field-rule" style="top:124px; left:76px; right:40px;"></div>
  <span class="field-label" style="top:140px; left:40px;">Date :</span>
  <div class="field-rule" style="top:156px; left:84px; right:40px;"></div>
  <span class="field-label field-label--underlined" style="top:172px; left:40px;">Location :</span>
  <div class="field-rule" style="top:188px; left:108px; right:40px;"></div>
  <p class="back__note">If you are unable to keep appointment, please contact<br>us as soon as possible. Call 877 555 0194
    <span class="back__web">www.DrDovanclinic.example</span></p>
</section>

</body>
</html>
```